Moravel Aesthetic Doctor

I require an elegant, luxurious looking business card for my aesthetic business. I am a doctor and that will set me aside from competitors. I am planning to provide home and spa based treatments to clients with high expectations. I have attached my logo.

```html
<!DOCTYPE html>
<html lang="en">
<head>
<meta charset="utf-8">
<title>Moravel Aesthetic Doctor – Business Card</title>
<link href="https://fonts.googleapis.com/css2?family=Marcellus&family=Open+Sans:wght@400;600&display=swap" rel="stylesheet">
<style>
  :root {
    --backdrop: #3b3b3d;
    --card: #1e1f22;
    --sky: #4fb3e8;
    --silver: #c9ced6;
    --white: #f2f4f6;
    --rule: #6b6f76;
  }
  * { margin: 0; padding: 0; box-sizing: border-box; }
  html, body { width: 799px; height: 1200px; overflow: hidden; }
  body {
    background: var(--backdrop);
    font-family: "Open Sans", sans-serif;
    display: flex;
    flex-direction: column;
    align-items: center;
    justify-content: center;
    gap: 90px;
  }
  .card {
    position: relative;
    width: 640px;
    height: 366px;
    background: var(--card);
    border-radius: 4px;
    box-shadow: 0 14px 30px rgba(0,0,0,.45);
    overflow: hidden;
  }
  .brand {
    position: absolute;
    left: 90px;
    top: 44px;
    display: flex;
    align-items: center;
    gap: 18px;
  }
  .brand-mark {
    width: 96px; height: 96px;
    border: 3px solid var(--silver);
    border-radius: 50%;
    flex: none;
  }
  .brand-name {
    font-family: "Marcellus", serif;
    color: var(--silver);
    line-height: 1;
  }
  .brand-name .primary { display: block; font-size: 62px; letter-spacing: 2px; }
  .brand-name .secondary { display: block; font-size: 23px; letter-spacing: 4.5px; margin-top: 6px; }

  .services {
    position: absolute;
    top: 192px; left: 0; right: 0;
    text-align: center;
    color: var(--white);
    font-size: 15px;
    line-height: 1.45;
  }
  .services .sep { margin: 0 8px; }
  .band {
    position: absolute;
    left: 0; right: 0;
    background: var(--sky);
  }
  .front .band {
    top: 252px; height: 42px;
    display: flex; align-items: center; justify-content: center;
    color: var(--white);
    font-size: 18px;
    letter-spacing: 1px;
  }

  .contact {
    position: absolute;
    left: 40px; top: 196px;
    right: 40px;
  }
  .person { color: var(--silver); font-size: 22px; }
  .person small { color: var(--sky); font-size: 10px; margin-left: 6px; font-weight: 600; }
  .qualification { color: var(--sky); font-size: 14px; margin-top: 2px; }
  .person-rule { height: 1px; background: var(--rule); margin: 6px 0 0 0; width: 100%; }
  .details {
    list-style: none;
    display: flex;
    gap: 26px;
    margin-top: 12px;
    color: var(--silver);
    font-size: 14px;
  }
  .details li { display: flex; align-items: center; gap: 7px; }
  .details svg { width: 16px; height: 16px; fill: none; stroke: var(--silver); stroke-width: 1.6; }
  .back .band { bottom: 22px; height: 22px; }
  .social {
    position: absolute;
    right: 40px; bottom: 14px;
    height: 38px; width: 96px;
    background: var(--sky);
    border-radius: 19px;
    display: flex; align-items: center; justify-content: center; gap: 12px;
  }
  .social span { width: 16px; height: 16px; border-radius: 50%; background: var(--white); }
</style>
</head>
<body>
  <section class="card front">
    <div class="brand">
      <div class="brand-mark"></div>
      <div class="brand-name"><span class="primary">MORAVEL</span><span class="secondary">AESTHETIC DOCTOR</span></div>
    </div>
    <p class="services">
      Dermal Injectables<span class="sep">|</span>Plasma Facials<span class="sep">|</span>Microneedling<br>
      Skin Boosters<span class="sep">|</span>Excessive Sweating
    </p>
    <div class="band">HOME AND SPA BASED TREATMENTS</div>
  </section>

  <section class="card back">
    <div class="brand">
      <div class="brand-mark"></div>
      <div class="brand-name"><span class="primary">MORAVEL</span><span class="secondary">AESTHETIC DOCTOR</span></div>
    </div>
    <div class="contact">
      <p class="person">Dr Elise Varden<small>MRCPCH MD</small></p>
      <p class="qualification">Australasian Diploma of Aesthetic Medicine</p>
      <div class="person-rule"></div>
      <ul class="details">
        <li><svg viewBox="0 0 16 16"><circle cx="8" cy="8" r="7"/><path d="M5.5 4.5l1.5 1.5-1 1c.6 1.2 1.5 2.1 2.7 2.7l1-1 1.5 1.5-1.2 1.2c-2.6-.6-4.6-2.6-5.2-5.2z"/></svg>0800 555 014</li>
        <li><svg viewBox="0 0 16 16"><rect x="1.5" y="3.5" width="13" height="9" rx="1"/><path d="M1.5 4l6.5 5 6.5-5"/></svg>elise@moravel.co.nz</li>
        <li><svg viewBox="0 0 16 16"><circle cx="8" cy="8" r="6.5"/><path d="M1.5 8h13M8 1.5c-3 3.5-3 9.5 0 13M8 1.5c3 3.5 3 9.5 0 13"/></svg>www.moravel.co.nz</li>
      </ul>
    </div>
    <div class="band"></div>
    <div class="social"><span></span><span></span></div>
  </section>
</body>
</html>
```